Website for a new t-shirt company called bolddawnapperal.com

We are looking for a talented web designer to create a website that aligns with our brand's message and identity centered around the theme of "Bold Dawn." The website should be modern, clean, and visually appealing while also being user-friendly and easy to navigate.

We will be using the Big Commerce platform for our online store section, so the designer should have experience in designing websites on this platform.

We would like the website to have the following elements:

A color scheme that aligns with the brand's identity and message
A homepage that showcases our products and message, with clear calls-to-action for visitors to explore further
A blog section that highlights our brand's philosophy and offers advice and tips for people looking to make positive changes in their lives
An "About Us" section that introduces our brand and team and offers insight into our mission and values
A contact form that allows visitors to easily get in touch with us for inquiries or support
We are open to creative suggestions and ideas from the designer, but we would like the website to have a modern and minimalist aesthetic that resonates with our target audience of 20 to 40-year-olds.

```html
<!DOCTYPE html>
<html lang="en">
<head>
<meta charset="utf-8">
<title>Bold Dawn – T Shirts</title>
<link rel="stylesheet" href="https://fonts.googleapis.com/css2?family=Special+Elite&family=Mulish:wght@400;500;600;700;800&display=swap">
<style>
:root{
  --orange:#f7872a;
  --ink:#111;
  --text:#333;
  --muted:#666;
  --soft:#f7f7f7;
  --band:#f4f2f2;
  --line:#e6e6e6;
  --footer:#0d0d0d;
  --white:#fff;
}
*{box-sizing:border-box;margin:0;padding:0}
html,body{width:1200px;height:3638px;overflow:hidden}
body{font-family:"Mulish",sans-serif;color:var(--text);background:var(--white);position:relative}
.abs{position:absolute}
.heading{font-family:"Special Elite",monospace;color:var(--ink);font-weight:400}
.btn{position:absolute;background:var(--orange);color:var(--white);font-weight:600;display:flex;align-items:center;justify-content:center;gap:8px}

/* header */
.site-header{position:absolute;top:0;left:0;width:1200px;height:96px}
.brand{position:absolute;left:134px;top:28px;font-size:30px;font-weight:800;color:var(--ink);display:flex;align-items:center;gap:10px}
.brand i{width:14px;height:14px;border-radius:50%;background:var(--orange);display:block}
.nav a{position:absolute;top:32px;height:27px;line-height:27px;font-size:15px;color:#222;text-decoration:none}
.nav .active{border:1px solid #222;padding:0 10px}
.tools svg{position:absolute;top:34px}

/* hero */
.hero{position:absolute;top:96px;left:0;width:1200px;height:577px;
  background:linear-gradient(90deg,#b9c0b4 0%,#7e8f6a 25%,#5d7440 48%,#b04a50 62%,#c75d64 72%,#57683a 88%,#344524 100%)}
.hero-title{position:absolute;left:170px;top:124px;font-size:96px;color:var(--white);line-height:1}
.hero-sub{position:absolute;left:174px;top:250px;width:430px;font-size:16px;font-weight:800;line-height:28px;color:var(--white);text-transform:uppercase}
.hero .btn{left:175px;top:332px;width:143px;height:49px;font-size:16px}
.slide-arrow{position:absolute;top:271px;width:51px;height:35px;background:var(--white);display:flex;align-items:center;justify-content:center}
.dots{position:absolute;top:536px;left:564px;display:flex;gap:9px}
.dots span{width:12px;height:12px;border-radius:50%;border:1.5px solid var(--white)}
.dots .on{background:#111;border-color:#111}

.section-title{position:absolute;width:1200px;left:0;text-align:center;font-size:38px}
.rule{position:absolute;left:574px;width:52px;height:2px;background:#111}
.pager{position:absolute;left:1022px;display:flex;gap:10px}

/* cards */
.product{position:absolute;top:823px;width:223px;height:457px;background:var(--soft);border:1px solid var(--line);text-align:center}
.product .photo{height:281px;background:linear-gradient(180deg,#fafafa,#ececec)}
.product .name{margin-top:22px;font-size:13px;line-height:20px;color:#222}
.product .price{margin-top:14px;font-size:16px;color:#222}
.product .btn{left:49px;top:397px;width:124px;height:33px;font-size:14px;font-weight:500}

/* about */
.about{position:absolute;top:1327px;left:0;width:1200px;height:443px;background:var(--band)}
.about-copy{position:absolute;left:131px;top:127px;width:462px;font-size:13px;line-height:20px;color:#444;text-align:justify}
.about .btn{left:134px;top:354px;width:100px;height:34px;font-size:12px;font-weight:800}
.value-box{position:absolute;left:647px;width:419px;height:158px;background:var(--white)}
.value-box .ring{position:absolute;left:30px;top:33px}
.value-box h3{position:absolute;left:153px;top:24px;font-size:22px}
.value-box p{position:absolute;left:153px;top:60px;width:232px;font-size:11.5px;line-height:16px;color:#555}

/* team */
.member{position:absolute;top:1916px;width:223px;height:347px;background:var(--soft);border:1px solid var(--line);text-align:center}
.member .photo{height:169px;background:linear-gradient(135deg,#8b98a6,#3f5f88 55%,#c9d1d8)}
.member h4{margin-top:25px;font-size:15px;font-weight:600;color:#111}
.member p{margin:12px auto 0;width:185px;font-size:11px;line-height:16px;color:#666}
.member .btn{left:73px;top:289px;width:77px;height:25px;font-size:12px;font-weight:500}

/* blog */
.blog{position:absolute;top:2308px;left:0;width:1200px;height:537px;background:var(--band)}
.post{position:absolute;top:141px;width:290px}
.post .photo{height:205px}
.post h4{margin-top:15px;font-size:16.5px;font-weight:600;line-height:22px;color:#222}
.post p{margin-top:9px;font-size:11px;line-height:17px;color:#666}
.post .btn{position:relative;margin-top:16px;width:84px;height:26px;font-size:12px;font-weight:500}

/* contact */
.field{position:absolute;border:1px solid #333;background:var(--white);font-size:13px;color:#444;padding:16px 15px}
.submit{left:549px;top:3277px;width:96px;height:34px;font-size:14px;font-weight:800}

/* footer */
.site-footer{position:absolute;top:3356px;left:0;width:1200px;height:282px;background:var(--footer);color:#ddd}
.site-footer h5{position:absolute;top:46px;font-size:14px;font-weight:600;color:var(--white)}
.site-footer ul{position:absolute;top:80px;list-style:none;font-size:12px;line-height:24px;color:#bbb}
.contact-line{position:absolute;left:165px;font-size:13px;line-height:21px;color:#ddd}
.pay{position:absolute;width:40px;height:24px;background:var(--white);border-radius:2px}
.foot-rule{position:absolute;left:131px;top:196px;width:935px;height:1px;background:#333}
.copyright{position:absolute;top:230px;width:1200px;text-align:center;font-size:11px;color:#ccc}
</style>
</head>
<body>

<header class="site-header">
  <div class="brand"><i></i>Bold Dawn</div>
  <nav class="nav">
    <a class="active" style="left:395px">Home</a>
    <a style="left:493px">About</a>
    <a style="left:583px">Shop All</a>
    <a style="left:693px">Blog</a>
    <a style="left:777px">Contact us</a>
  </nav>
  <div class="tools">
    <svg style="left:945px" width="20" height="20" viewBox="0 0 20 20" fill="none" stroke="#222" stroke-width="1.5"><circle cx="10" cy="6" r="4"/><path d="M2 19c1-5 4-7 8-7s7 2 8 7z"/></svg>
    <svg style="left:996px" width="20" height="20" viewBox="0 0 20 20" fill="none" stroke="#222" stroke-width="1.6"><circle cx="8.5" cy="8.5" r="6.5"/><path d="M13.5 13.5L19 19"/></svg>
    <svg style="left:1046px" width="22" height="20" viewBox="0 0 22 20" fill="none" stroke="#222" stroke-width="1.5"><path d="M1 2h3l3 11h11l2-8H6"/><circle cx="8.5" cy="17" r="1.5"/><circle cx="16.5" cy="17" r="1.5"/></svg>
  </div>
</header>

<section class="hero" role="img" aria-label="Man in sunglasses wearing a red patterned t-shirt on a tree-lined street">
  <h1 class="heading hero-title">T Shirt</h1>
  <p class="hero-sub">Lorem Ipsum is simply dummy text of the printing and typesetting industry</p>
  <a class="btn">SHOP NOW</a>
  <div class="slide-arrow" style="left:37px"><svg width="12" height="14" viewBox="0 0 12 14"><path d="M8 2L3 7l5 5" fill="none" stroke="#111" stroke-width="2"/></svg></div>
  <div class="slide-arrow" style="left:1118px"><svg width="12" height="14" viewBox="0 0 12 14"><path d="M4 2l5 5-5 5" fill="none" stroke="#111" stroke-width="2"/></svg></div>
  <div class="dots"><span class="on"></span><span></span><span></span><span></span></div>
</section>

<h2 class="heading section-title" style="top:710px">Featured Products</h2>
<div class="rule" style="top:779px"></div>
<div class="pager" style="top:781px">
  <svg width="16" height="12" viewBox="0 0 16 12"><path d="M15 6H2M6 2L2 6l4 4" fill="none" stroke="#aaa" stroke-width="1.4"/></svg>
  <svg width="16" height="12" viewBox="0 0 16 12"><path d="M1 6h13M10 2l4 4-4 4" fill="none" stroke="#111" stroke-width="1.4"/></svg>
</div>

<div class="product" style="left:131px">
  <div class="photo" role="img" aria-label="Man in a red polo shirt"></div>
  <p class="name">Lorem Ipsum is simply<br>dummy text of the printi</p>
  <p class="price">$210.00</p>
  <a class="btn"><svg width="16" height="15" viewBox="0 0 22 20" fill="none" stroke="#fff" stroke-width="1.8"><path d="M1 2h3l3 11h11l2-8H6"/><circle cx="8.5" cy="17" r="1.5"/><circle cx="16.5" cy="17" r="1.5"/></svg>Add to Cart</a>
</div>
<div class="product" style="left:367px">
  <div class="photo" role="img" aria-label="Woman in a pink t-shirt"></div>
  <p class="name">Lorem Ipsum is simply<br>dummy text of the printi</p>
  <p class="price">$210.00</p>
  <a class="btn"><svg width="16" height="15" viewBox="0 0 22 20" fill="none" stroke="#fff" stroke-width="1.8"><path d="M1 2h3l3 11h11l2-8H6"/><circle cx="8.5" cy="17" r="1.5"/><circle cx="16.5" cy="17" r="1.5"/></svg>Add to Cart</a>
</div>
<div class="product" style="left:604px">
  <div class="photo" role="img" aria-label="Man in an olive green t-shirt"></div>
  <p class="name">Lorem Ipsum is simply<br>dummy text of the printi</p>
  <p class="price">$210.00</p>
  <a class="btn"><svg width="16" height="15" viewBox="0 0 22 20" fill="none" stroke="#fff" stroke-width="1.8"><path d="M1 2h3l3 11h11l2-8H6"/><circle cx="8.5" cy="17" r="1.5"/><circle cx="16.5" cy="17" r="1.5"/></svg>Add to Cart</a>
</div>
<div class="product" style="left:842px">
  <div class="photo" role="img" aria-label="Man in a white t-shirt"></div>
  <p class="name">Lorem Ipsum is simply<br>dummy text of the printi</p>
  <p class="price">$210.00</p>
  <a class="btn"><svg width="16" height="15" viewBox="0 0 22 20" fill="none" stroke="#fff" stroke-width="1.8"><path d="M1 2h3l3 11h11l2-8H6"/><circle cx="8.5" cy="17" r="1.5"/><circle cx="16.5" cy="17" r="1.5"/></svg>Add to Cart</a>
</div>

<section class="about">
  <h2 class="heading abs" style="left:131px;top:46px;font-size:38px">About Us</h2>
  <div class="abs" style="left:131px;top:99px;width:57px;height:2px;background:#111"></div>
  <p class="about-copy">Sed ut perspiciatis unde omnis iste natus error sit voluptatem accusantium doloremque laudantium, totam rem aperiam, eaque ipsa quae ab illo inventore veritatis et quasi architecto beatae vitae dicta sunt explicabo. Nemo enim ipsam voluptatem quia voluptas sit aspernatur aut odit aut fugit, sed quia consequuntur magni dolores eos qui ratione voluptatem sequi nesciunt. Neque porro quisquam est, qui dolorem ipsum quia dolor sit amet, consectetur, adipisci velit, sed quia non numquam eius modi tempora incidunt ut labore et dolore magnam aliquam quaerat voluptatem. Ut enim ad minima veniam, quis nostrum exercitationem ullam corporis suscipit laboriosam, nisi ut aliquid ex ea commodi consequatur</p>
  <a class="btn">READ MORE</a>

  <div class="value-box" style="top:61px">
    <svg class="ring" width="94" height="94" viewBox="0 0 94 94" fill="none"><circle cx="47" cy="47" r="45" stroke="#111" stroke-width="2"/><circle cx="47" cy="49" r="22" stroke="var(--orange)" stroke-width="2.5"/><circle cx="47" cy="49" r="14" stroke="var(--orange)" stroke-width="2.5"/><circle cx="47" cy="49" r="6" stroke="var(--orange)" stroke-width="2.5"/><path d="M47 49l18-18M60 30l6 1-1 6" stroke="var(--orange)" stroke-width="2.5"/></svg>
    <h3 class="heading">Our Mission</h3>
    <p>Sed ut perspiciatis unde omnis iste natus error sit voluptatem accusantium dolor emque laudantium, totam rem aperiam, eaque ipsa quae ab illo</p>
  </div>
  <div class="value-box" style="top:233px">
    <svg class="ring" width="94" height="94" viewBox="0 0 94 94" fill="none"><circle cx="47" cy="47" r="45" stroke="#111" stroke-width="2"/><path d="M30 42l7-9h20l7 9-17 22z M30 42h34 M40 42l7 22 7-22 M37 33l3 9 7-9 7 9 3-9" stroke="var(--orange)" stroke-width="2.2" stroke-linejoin="round"/><path d="M47 20v7M36 24l3 5M58 24l-3 5" stroke="var(--orange)" stroke-width="2.2"/></svg>
    <h3 class="heading">Values</h3>
    <p>Sed ut perspiciatis unde omnis iste natus error sit voluptatem accusantium dolor emque laudantium, totam rem aperiam, eaque ipsa quae ab illo</p>
  </div>
</section>

<h2 class="heading section-title" style="top:1806px">Our Team</h2>
<div class="rule" style="top:1872px"></div>
<div class="pager" style="top:1875px">
  <svg width="16" height="12" viewBox="0 0 16 12"><path d="M15 6H2M6 2L2 6l4 4" fill="none" stroke="#aaa" stroke-width="1.4"/></svg>
  <svg width="16" height="12" viewBox="0 0 16 12"><path d="M1 6h13M10 2l4 4-4 4" fill="none" stroke="#111" stroke-width="1.4"/></svg>
</div>

<div class="member" style="left:131px">
  <div class="photo" role="img" aria-label="Team member portrait in a bright office" style="background:linear-gradient(135deg,#e8e4de,#7fb0d8 55%,#d9d4cc)"></div>
  <h4>Daniel Moreno</h4>
  <p>Sed ut perspiciatis unde omnis iste natus error sit voluptatem accu santium doloremque.</p>
  <a class="btn">View Bio</a>
</div>
<div class="member" style="left:369px">
  <div class="photo" role="img" aria-label="Team member portrait in a blue suit"></div>
  <h4>Whitfield</h4>
  <p>Sed ut perspiciatis unde omnis iste natus error sit voluptatem accu santium doloremque.</p>
  <a class="btn">View Bio</a>
</div>
<div class="member" style="left:607px">
  <div class="photo" role="img" aria-label="Team member portrait in a modern office" style="background:linear-gradient(135deg,#5b6670,#9aa5ad 55%,#3b4550)"></div>
  <h4>Owen R. Hale</h4>
  <p>Sed ut perspiciatis unde omnis iste natus error sit voluptatem accu santium doloremque.</p>
  <a class="btn">View Bio</a>
</div>
<div class="member" style="left:844px">
  <div class="photo" role="img" aria-label="Team member portrait in a navy blazer" style="background:linear-gradient(135deg,#b5bcc0,#2e3a4c 55%,#d0d4d6)"></div>
  <h4>Marcus</h4>
  <p>Sed ut perspiciatis unde omnis iste natus error sit voluptatem accu santium doloremque.</p>
  <a class="btn">View Bio</a>
</div>

<section class="blog">
  <h2 class="heading section-title" style="top:37px">Latest Blog</h2>
  <div class="rule" style="top:106px"></div>
  <article class="post" style="left:131px">
    <div class="photo" role="img" aria-label="Young man in a beige t-shirt" style="background:linear-gradient(180deg,#dcdcda,#c8ad8a 70%,#b99c78)"></div>
    <h4>Sed ut perspiciatis unde omnis iste natus error</h4>
    <p>Sed ut perspiciatis unde omnis iste natus error sit voluptatem accu santium doloremque.</p>
    <a class="btn">Read More</a>
  </article>
  <article class="post" style="left:455px">
    <div class="photo" role="img" aria-label="Woman in a graphic t-shirt sitting on a stool" style="background:linear-gradient(90deg,#f3efe8,#e4dccf 50%,#d7c9b6)"></div>
    <h4>Sed ut perspiciatis unde omnis iste natus error</h4>
    <p>Sed ut perspiciatis unde omnis iste natus error sit voluptatem accu santium doloremque.</p>
    <a class="btn">Read More</a>
  </article>
  <article class="post" style="left:776px">
    <div class="photo" role="img" aria-label="Man in a black t-shirt and cap against a stone wall" style="background:linear-gradient(135deg,#4c5666,#7d8591 50%,#2c3038)"></div>
    <h4>Sed ut perspiciatis unde omnis iste natus error</h4>
    <p>Sed ut perspiciatis unde omnis iste natus error sit voluptatem accu santium doloremque.</p>
    <a class="btn">Read More</a>
  </article>
</section>

<h2 class="heading section-title" style="top:2885px">Contact Us</h2>
<div class="rule" style="top:2953px"></div>
<form>
  <div class="field" style="left:250px;top:2986px;width:341px;height:49px">First Name</div>
  <div class="field" style="left:607px;top:2986px;width:341px;height:49px">Last Name</div>
  <div class="field" style="left:250px;top:3049px;width:341px;height:49px">Email id</div>
  <div class="field" style="left:607px;top:3049px;width:341px;height:49px">Phone</div>
  <div class="field" style="left:250px;top:3116px;width:697px;height:139px">Message</div>
  <a class="btn submit">SUBMIT</a>
</form>

<footer class="site-footer">
  <svg class="abs" style="left:132px;top:48px" width="16" height="20" viewBox="0 0 16 20" fill="none" stroke="#ddd" stroke-width="1.3"><path d="M8 19s7-7 7-11A7 7 0 0 0 1 8c0 4 7 11 7 11z"/><circle cx="8" cy="8" r="2.5"/></svg>
  <p class="contact-line" style="top:44px">Lorem ipsum dolor sit amet,<br>consectetur, LA 70512</p>
  <svg class="abs" style="left:131px;top:116px" width="19" height="19" viewBox="0 0 20 20" fill="none" stroke="#ddd" stroke-width="1.3"><path d="M4 1l3 4-2 2c1 3 4 6 7 7l2-2 4 3-2 3C9 18 2 11 1 4z"/></svg>
  <p class="contact-line" style="top:112px">Call<br>+1 555 010 2040</p>

  <h5 style="left:405px">Quick Links</h5>
  <ul style="left:405px"><li>About</li><li>Changelog</li><li>Shipping &amp; Returns</li></ul>

  <h5 style="left:631px">Categories</h5>
  <ul style="left:631px"><li>Women</li><li>Men</li><li>Kids</li><li>Accessories</li></ul>

  <h5 style="left:823px">Payment Method</h5>
  <div class="pay" style="left:823px;top:80px"></div>
  <div class="pay" style="left:874px;top:80px"></div>
  <div class="pay" style="left:924px;top:80px"></div>
  <div class="pay" style="left:974px;top:80px"></div>
  <div class="pay" style="left:1024px;top:80px"></div>
  <div class="pay" style="left:823px;top:113px"></div>
  <div class="pay" style="left:874px;top:113px"></div>

  <div class="foot-rule"></div>
  <p class="copyright">Copyright © 2023 All Rights Reserved</p>
</footer>

</body>
</html>
```